Infographic for Commercial Painting and Flooring Company

We need an Infographic that shows a compelling argument for signing on with Dravimex for a maintenance contract vs a project. The infographic should be easily understood visually so sell the story we have provided. 1) What does the quick view give me? 2) Am I interested in this? 3) Does this bring me any value? 4) Is this “everything I have seen before or something new and different”? Included here is a word document called Maintenance vs Project Notes with the written content and instructions, a logo, and two other marketing pieces they currently use so you can see how their brand is being used. Colors should be on brand. I'd like to get this done ASAP if possible. We do not want this piece to look busy.

I added two images called Sample 1 and Sample 2 to portray the types of infographics we like. Simple and clear. Love the watch with the pie chart built in....a smaller version of that would be great for us based on the notes document I provided.

Target Market(s)

Facilities Manufacturers and owners of manufacturing facilities

Font styles to use
Sans Serif

Colors

Designer to choose colors to be used in the design.

Requirements
Must have
• Simple, clean, tell a clear story
Nice to have
• Iconography, pie chart, Men in hard hat
Should not have
• Too many colors. Stick with the brand colors and maybe a few others. Don't want it too look to busy.

```html
<!DOCTYPE html>
<html lang="en">
<head>
<meta charset="utf-8">
<title>Maintenance Program vs. Project</title>
<link href="https://fonts.googleapis.com/css2?family=Oswald:wght@500;600;700&family=Arimo:wght@400;700&family=Open+Sans:wght@700;800&family=Source+Sans+3:wght@400;600&display=swap" rel="stylesheet">
<style>
  :root {
    --navy: #1c4882;
    --green: #b2bb34;
    --pale-green: #d5d68a;
    --gray: #c9c9c9;
    --sky: #8fb3e0;
    --steel: #6a93bf;
    --slate: #3e659b;
    --mid-blue: #3d7cc0;
    --bg: #cae8f8;
    --white: #ffffff;
  }
  * { margin: 0; padding: 0; box-sizing: border-box; }
  html, body { width: 1200px; height: 1200px; overflow: hidden; background: var(--bg); }
  .flyer {
    position: absolute; left: 142px; top: 8px;
    width: 1246px; height: 1612px;
    transform: scale(0.735); transform-origin: top left;
    background: var(--white);
    font-family: "Arimo", Arial, sans-serif;
  }
  .abs { position: absolute; }
  .title-bar {
    left: 0; top: 0; width: 1246px; height: 90px; background: var(--navy);
    color: var(--white); font-family: "Oswald", sans-serif; font-weight: 700;
    font-size: 68px; line-height: 90px; text-align: center; letter-spacing: 0.5px;
  }
  .title-bar .vs { font-size: 40px; margin: 0 14px; }
  .time-banner { left: 245px; top: 133px; width: 1001px; height: 173px; }
  .time-banner-text { left: 300px; top: 150px; width: 940px; text-align: center; }
  .time-banner-text .question { color: var(--navy); font-weight: 700; font-size: 35px; line-height: 44px; }
  .time-banner-text .answer { color: var(--white); font-family: "Source Sans 3", sans-serif; font-size: 35px; margin-top: 8px; letter-spacing: 0.5px; }
  .time-banner-text .answer u { text-underline-offset: 6px; }
  .worker-art {
    left: 5px; top: 95px; width: 225px; height: 435px;
    background: linear-gradient(180deg, #f1c232 0%, #f5d7b0 25%, #ffffff 45%, #1c4882 85%);
    border-radius: 8px;
  }
  .hours-arrow { left: 0; top: 530px; width: 548px; height: 163px; }
  .hours-text {
    left: 10px; top: 553px; width: 510px; text-align: center;
    color: var(--green); font-weight: 700; font-size: 29px; line-height: 35px;
  }
  .hours-text strong { color: var(--white); font-size: 36px; }
  .watch { left: 550px; top: 350px; width: 680px; height: 420px; }
  .step-label { position: absolute; font-weight: 700; font-size: 20px; line-height: 25px; color: #222; }
  .step-label b { color: var(--navy); }
  .stat-box {
    top: 784px; height: 136px; border: 3px solid var(--navy); border-radius: 26px; padding: 7px;
  }
  .stat-box div {
    height: 100%; background: var(--green); border-radius: 20px; color: var(--white);
    font-weight: 700; font-size: 24px; line-height: 30px; text-align: center;
    display: flex; align-items: center; justify-content: center;
  }
  .once-band {
    left: 0; top: 935px; width: 1246px; height: 64px; background: var(--green);
    color: var(--navy); font-family: "Oswald", sans-serif; font-weight: 600; font-size: 50px;
    line-height: 64px; text-align: center;
  }
  .team-panel { left: 0; top: 1014px; width: 1246px; height: 278px; background: var(--navy); color: var(--white); }
  .team-heading { position: absolute; top: 22px; width: 100%; text-align: center; font-family: "Open Sans", sans-serif; font-weight: 800; font-size: 40px; }
  .value { position: absolute; top: 105px; width: 360px; text-align: center; }
  .value svg { display: block; margin: 0 auto; }
  .value span { display: block; margin-top: 8px; font-family: "Open Sans", sans-serif; font-weight: 700; font-size: 39px; }
  .benefits { left: 0; top: 1306px; width: 1246px; height: 220px; background: var(--green); }
  .benefit-list { position: absolute; top: 20px; list-style: none; color: var(--navy); font-family: "Source Sans 3", sans-serif; font-size: 25px; }
  .benefit-list li { height: 45px; line-height: 45px; }
  .benefit-list li::before { content: "\2713"; margin-right: 10px; }
  .footer-bar { left: 0; top: 1512px; width: 1246px; height: 100px; }
  .footer-text {
    left: 0; top: 1525px; width: 870px; height: 87px; line-height: 87px; text-align: center;
    color: var(--white); font-family: "Oswald", sans-serif; font-weight: 500; font-size: 38px;
  }
  .footer-text u { text-underline-offset: 5px; }
  .brand { left: 1015px; top: 1545px; display: flex; align-items: center; gap: 10px; color: var(--navy); font-family: "Arimo", sans-serif; font-weight: 700; font-size: 32px; }
  .brand i { width: 40px; height: 40px; background: var(--green); display: block; }
</style>
</head>
<body>
<div class="flyer">
  <h1 class="abs title-bar">MAINTENANCE PROGRAM<span class="vs">VS.</span>PROJECT?</h1>

  <svg class="abs time-banner" viewBox="0 0 1001 173" aria-hidden="true">
    <polygon points="55,0 1001,0 1001,173 55,173 0,86" fill="var(--green)"/>
  </svg>
  <div class="abs time-banner-text">
    <p class="question">IMAGINE WHAT YOU COULD DO WITH AN EXTRA<br>30% MORE TIME EACH YEAR?</p>
    <p class="answer">TIME YOU GET BACK BY ONBOARDING <u>ONCE</u></p>
  </div>

  <div class="abs worker-art" role="img" aria-label="Illustration of a puzzled worker in a yellow hard hat and tie holding rolled plans"></div>

  <svg class="abs hours-arrow" viewBox="0 0 548 163" aria-hidden="true">
    <polygon points="0,0 490,0 548,82 490,163 0,163" fill="var(--navy)"/>
  </svg>
  <p class="abs hours-text">IT TAKES <strong>30+ HOURS</strong> TO SOURCE AND ONBOARD THE MOST QUALIFIED VENDOR...YIKES!</p>

  <svg class="abs watch" viewBox="550 350 680 420" aria-label="Stopwatch pie chart of 30 hours spent onboarding a vendor">
    <g transform="translate(890,552)">
      <rect x="-7" y="-178" width="14" height="22" fill="var(--navy)"/>
      <rect x="-18" y="-186" width="36" height="10" rx="2" fill="var(--navy)"/>
      <g transform="rotate(45)">
        <rect x="-7" y="-180" width="14" height="22" fill="var(--navy)"/>
        <circle cx="0" cy="-178" r="20" fill="none" stroke="var(--navy)" stroke-width="2"/>
      </g>
      <path d="M0,0 L0,-158 A158,158 0 0 1 117.4,-105.7Z" fill="var(--gray)"/>
      <path d="M0,0 L117.4,-105.7 A158,158 0 0 1 117.4,105.7Z" fill="var(--green)"/>
      <path d="M0,0 L117.4,105.7 A158,158 0 0 1 32.9,154.5Z" fill="var(--sky)"/>
      <path d="M0,0 L32.9,154.5 A158,158 0 0 1 -92.9,127.8Z" fill="var(--steel)"/>
      <path d="M0,0 L-92.9,127.8 A158,158 0 0 1 -136.8,79Z" fill="var(--slate)"/>
      <path d="M0,0 L-136.8,79 A158,158 0 0 1 -150.3,-48.8Z" fill="var(--mid-blue)"/>
      <path d="M0,0 L-150.3,-48.8 A158,158 0 0 1 -92.9,-127.8Z" fill="var(--navy)"/>
      <path d="M0,0 L-92.9,-127.8 A158,158 0 0 1 0,-158Z" fill="var(--pale-green)"/>
      <g fill="#fff" font-family="Arimo, sans-serif" font-weight="700" text-anchor="middle">
        <text x="57" y="-110" font-size="30">4</text><text x="57" y="-94" font-size="13">hrs</text>
        <text x="128" y="-4" font-size="30">7</text><text x="128" y="12" font-size="13">hrs</text>
        <text x="74" y="98" font-size="30">3</text><text x="74" y="114" font-size="13">hrs</text>
        <text x="-29" y="120" font-size="30">4</text><text x="-29" y="136" font-size="13">hrs</text>
        <text x="-101" y="75" font-size="30">2</text><text x="-101" y="91" font-size="13">hrs</text>
        <text x="-131" y="8" font-size="30">4</text><text x="-131" y="24" font-size="13">hrs</text>
        <text x="-104" y="-68" font-size="30">3</text><text x="-104" y="-52" font-size="13">hrs</text>
        <text x="-42" y="-117" font-size="30">3</text><text x="-42" y="-101" font-size="13">hrs</text>
      </g>
      <g stroke="var(--navy)" stroke-width="1.5" fill="var(--navy)">
        <line x1="76" y1="-147" x2="90" y2="-172"/><circle cx="90" cy="-172" r="3"/>
        <line x1="160" y1="0" x2="190" y2="0"/><circle cx="190" cy="0" r="3"/>
        <line x1="96" y1="128" x2="113" y2="152"/><circle cx="113" cy="152" r="3"/>
        <line x1="-40" y1="155" x2="-45" y2="182"/><circle cx="-45" cy="182" r="3"/>
        <line x1="-120" y1="105" x2="-153" y2="122"/><circle cx="-153" cy="122" r="3"/>
        <line x1="-158" y1="5" x2="-188" y2="5"/><circle cx="-188" cy="5" r="3"/>
        <line x1="-130" y1="-105" x2="-150" y2="-120"/><circle cx="-150" cy="-120" r="3"/>
        <line x1="-50" y1="-150" x2="-61" y2="-182"/><circle cx="-61" cy="-182" r="3"/>
      </g>
    </g>
  </svg>
  <p class="step-label" style="left:983px;top:358px"><b>1.</b>Source Vendors</p>
  <p class="step-label" style="left:1086px;top:541px"><b>2.</b>Schedule<br>&nbsp;Walkthrough</p>
  <p class="step-label" style="left:1018px;top:697px"><b>3.</b>Review Estimates</p>
  <p class="step-label" style="left:835px;top:743px"><b>4.</b>Clarify scope</p>
  <p class="step-label" style="left:580px;top:654px;text-align:center"><b>5.</b>Present to<br>Decision Maker</p>
  <p class="step-label" style="left:568px;top:546px;text-align:center"><b>6.</b>Negotiate<br>with Vendors</p>
  <p class="step-label" style="left:615px;top:421px;text-align:center"><b>7.</b>Award &amp;<br>Purchasing</p>
  <p class="step-label" style="left:675px;top:348px;text-align:center"><b>8.</b>On-Boarding<br>Paperwork</p>

  <div class="abs stat-box" style="left:193px;width:417px"><div>20 Projects = 600 Hours or<br>30% of Your Time Per Year…<br>UGGH!</div></div>
  <div class="abs stat-box" style="left:666px;width:398px"><div>On-Boarding Once = 1.5 %<br>of Your Time for the entire<br>year….FOR REAL!</div></div>

  <h2 class="abs once-band">DO IT ONCE! WITH A PREVENTIVE&nbsp; MAINTENANCE PROGRAM</h2>

  <section class="abs team-panel">
    <h3 class="team-heading">WE BECOME AN EXTENSION OF YOUR TEAM</h3>
    <div class="value" style="left:-15px">
      <svg width="110" height="100" viewBox="0 0 110 100" aria-hidden="true">
        <g fill="none" stroke="var(--green)" stroke-width="10">
          <path d="M20,42 A36,36 0 0 1 86,30"/><path d="M90,58 A36,36 0 0 1 24,70"/>
        </g>
        <polygon points="78,18 100,36 74,42" fill="var(--green)"/>
        <polygon points="32,82 10,64 36,58" fill="var(--green)"/>
        <circle cx="55" cy="50" r="15" fill="var(--green)"/>
      </svg>
      <span>CONSISTENCY</span>
    </div>
    <div class="value" style="left:445px">
      <svg width="110" height="100" viewBox="0 0 110 100" aria-hidden="true">
        <g fill="none" stroke="var(--green)" stroke-width="9" stroke-linecap="round">
          <circle cx="42" cy="50" r="30"/><line x1="64" y1="72" x2="88" y2="94"/>
          <polyline points="22,58 36,44 48,56 88,12"/>
        </g>
        <polygon points="72,6 96,4 94,28" fill="var(--green)"/>
      </svg>
      <span>PREDICTABILITY</span>
    </div>
    <div class="value" style="left:915px">
      <svg width="110" height="100" viewBox="0 0 110 100" aria-hidden="true">
        <path d="M55,4 L92,16 L92,50 C92,74 74,90 55,98 C36,90 18,74 18,50 L18,16Z" fill="none" stroke="var(--green)" stroke-width="9"/>
        <polyline points="38,52 51,66 74,38" fill="none" stroke="var(--green)" stroke-width="9"/>
      </svg>
      <span>RELIABILITY</span>
    </div>
  </section>

  <section class="abs benefits">
    <ul class="benefit-list" style="left:90px">
      <li>Adherance to Safety as Our #1 Objective</li>
      <li>Adapts to “<u>Your</u>” Scheduling Requirements</li>
      <li>A Single Point of Communication</li>
      <li>Work Order Integration &amp; Tracking</li>
    </ul>
    <ul class="benefit-list" style="left:645px">
      <li>Rapid Response Time</li>
      <li>A Dedicated Field Team Who Knows Your Facility</li>
      <li>Equal Priority for All Tasks (Big or Small)</li>
      <li>Customized Billing and Future Budget Building</li>
    </ul>
  </section>

  <svg class="abs footer-bar" viewBox="0 0 1246 100" aria-hidden="true">
    <rect x="0" y="13" width="1246" height="87" fill="var(--navy)"/>
    <polygon points="1000,0 1246,0 1246,100 955,100" fill="#f4f4f4"/>
  </svg>
  <p class="abs footer-text">WE OPERATE THE WAY <u>YOU</u> OPERATE!</p>
  <div class="abs brand"><i></i>Dravimex</div>
</div>
</body>
</html>
```